BOLD & MINIMALIST DESIGN NEEDED

We want a very bold but minimalistic business card design that is impactful and utilizes both sides of the business card. Our current logo is included for your use.

We want bold fonts and good use of negative space. We don't want the logo to overpower the design.

Target Market(s)

Professionals who are building new commercial buildings.

Industry/Entity Type

Construction

Contact Information for Business Card

Name, Title, email, office phone, cell phone, website

Font styles to use
Serif
Sans Serif

Requirements
Must have
• Bold design!

```html
<!DOCTYPE html>
<html lang="en">
<head>
<meta charset="utf-8">
<title>Ridgeline Design + Build — Business Card</title>
<link href="https://fonts.googleapis.com/css2?family=Montserrat:wght@400;500;700;800&display=swap" rel="stylesheet">
<style>
  :root {
    --backdrop: #d3d3cf;
    --card-white: #ffffff;
    --card-black: #141414;
    --ink: #1a1a1a;
    --brand-green: #7dc242;
    --muted: #2b2b2b;
  }
  * { margin: 0; padding: 0; box-sizing: border-box; }
  html, body {
    width: 1200px; height: 801px; overflow: hidden;
    background: var(--backdrop);
    font-family: 'Montserrat', sans-serif;
  }
  .stage {
    width: 1200px; height: 801px;
    display: flex; align-items: center; justify-content: center; gap: 48px;
  }
  .card {
    width: 532px; height: 304px;
    position: relative;
    border-bottom: 4px solid var(--brand-green);
    box-shadow: 0 14px 30px rgba(0,0,0,0.22);
    overflow: hidden;
  }
  /* Front */
  .card-front {
    background: var(--card-white);
    display: flex; align-items: center;
    padding: 0 34px 0 38px;
  }
  .wordmark {
    width: 200px;
    display: flex; align-items: center; gap: 10px;
  }
  .wordmark-dot {
    width: 16px; height: 16px; border-radius: 50%;
    background: var(--brand-green); flex: none;
  }
  .wordmark-name {
    font-weight: 800; font-size: 19px; line-height: 1.15;
    color: var(--ink); letter-spacing: 0.5px; text-transform: uppercase;
  }
  .divider {
    width: 2px; height: 118px; background: var(--brand-green);
    margin: 0 26px 0 14px; flex: none;
  }
  .contact-block { color: var(--muted); }
  .person-name {
    font-weight: 700; font-size: 21px; color: var(--brand-green);
    letter-spacing: 1px; text-transform: uppercase;
  }
  .person-title {
    font-weight: 500; font-size: 11px; letter-spacing: 1px;
    text-transform: uppercase; margin: 2px 0 14px;
  }
  .contact-list { list-style: none; }
  .contact-list li {
    display: flex; align-items: center; gap: 7px;
    font-size: 11.5px; line-height: 1.6;
  }
  .contact-list svg { width: 11px; height: 11px; flex: none; }
  .accent { color: var(--brand-green); }
  /* Back */
  .card-back {
    background: var(--card-black);
    display: flex; align-items: center; justify-content: center;
  }
  .pattern-field {
    position: absolute; inset: 0;
    background: linear-gradient(135deg, #202020 0%, #161616 50%, #0e0e0e 100%);
  }
  .back-wordmark {
    position: relative;
    display: flex; align-items: center; gap: 12px;
  }
  .back-wordmark .wordmark-name { color: var(--card-white); font-size: 24px; }
</style>
</head>
<body>
<main class="stage">
  <section class="card card-front" aria-label="Card front">
    <div class="wordmark">
      <span class="wordmark-dot"></span>
      <span class="wordmark-name">Ridgeline<br>Design + Build</span>
    </div>
    <div class="divider"></div>
    <div class="contact-block">
      <p class="person-name">Marcus Hale</p>
      <p class="person-title">Owner</p>
      <ul class="contact-list">
        <li>
          <svg viewBox="0 0 12 12"><path d="M2.5 1 L4.5 1 L5.2 3.4 L4 4.3 Q5 6.6 7.7 8 L8.6 6.8 L11 7.5 L11 9.5 Q10.5 11 9 11 Q1 10 1 2.6 Q1 1.2 2.5 1Z" fill="var(--brand-green)"/></svg>
          (555) 014-2270
        </li>
        <li>
          <svg viewBox="0 0 12 12"><rect x="1" y="5" width="10" height="6" rx="1.5" fill="var(--brand-green)"/><path d="M1 4 Q6 0 11 4 L9.5 5 L2.5 5Z" fill="var(--brand-green)"/></svg>
          (555) 014-2270
        </li>
        <li>
          <svg viewBox="0 0 12 12"><rect x="1" y="2.5" width="10" height="7" fill="none" stroke="var(--brand-green)" stroke-width="1.2"/><path d="M1 2.5 L6 6.5 L11 2.5" fill="none" stroke="var(--brand-green)" stroke-width="1.2"/></svg>
          ridgelinebuild@mail.com
        </li>
        <li>
          <svg viewBox="0 0 12 12"><circle cx="6" cy="6" r="5" fill="none" stroke="var(--brand-green)" stroke-width="1.2"/><ellipse cx="6" cy="6" rx="2.2" ry="5" fill="none" stroke="var(--brand-green)" stroke-width="1"/><line x1="1" y1="6" x2="11" y2="6" stroke="var(--brand-green)" stroke-width="1"/></svg>
          www.<span class="accent">ridgelinebuild</span>.com
        </li>
      </ul>
    </div>
  </section>

  <section class="card card-back" aria-label="Card back">
    <div class="pattern-field" role="img" aria-label="Repeating embossed brand pattern in dark grey across the card"></div>
    <div class="back-wordmark">
      <span class="wordmark-dot"></span>
      <span class="wordmark-name">Ridgeline</span>
    </div>
  </section>
</main>
</body>
</html>
```